Business Cards Design for the electrical wholesaler: clean bold dynamic :)

We need a business card design that would follow our latest brand guidelines. As an electrical wholesaler we want to bring a fresh look and feel into the industry. The design should be clean bold and dynamic. It should come alive with the renewed energy of our green colour. Our grey colour should keep things balanced and complement the notion of maturity and responsibility. We employ Lato as a corporate font however are not bound by this font and we’re open to interpretation here.

Target Market(s)

Electrical contractors

Industry/Entity Type

Business

Contact Information for Business Card

Logo
Name & Surname: Halyna Dorosh
Job Title: Director of Marketing
Email: halya.dorosh@quillmail.example
Cell phone: XXX.XXX.XXXX
Address: 20517 - 87 Ave. Edmonton, AB, Canada. T6K 4N8
Business Phone: 780.555.0184
Website: www.brovix.example

Font styles to use
Other font styles liked:
• Lato

Requirements
Must have
• Logo & website
Nice to have
• Brand elements - some of them you may find in the attached Brand Guidelines (e.g. three lines on the background signifying "W")

```html
<!DOCTYPE html>
<html lang="en">
<head>
<meta charset="utf-8">
<title>Brovix Business Cards</title>
<link rel="stylesheet" href="https://fonts.googleapis.com/css2?family=Lato:wght@400;700&display=swap">
<style>
  :root {
    --stage: #9a9a9a;
    --charcoal: #4a4b4d;
    --charcoal-deep: #3f4042;
    --green: #7cc242;
    --paper: #ffffff;
    --paper-shade: #ececec;
    --ink: #3d3e40;
    --rule: #b5b5b5;
  }
  * { margin: 0; padding: 0; box-sizing: border-box; }
  html, body { width: 1200px; height: 900px; overflow: hidden; }
  body {
    background: var(--stage);
    font-family: "Lato", sans-serif;
    position: relative;
  }
  .card {
    position: absolute;
    left: 320px;
    width: 560px;
    height: 320px;
    border-radius: 18px;
    overflow: hidden;
    box-shadow: 0 6px 18px rgba(0,0,0,0.25);
  }
  /* Back side */
  .card--back {
    top: 100px;
    background: linear-gradient(160deg, var(--charcoal) 0%, var(--charcoal-deep) 100%);
  }
  .card--back .brand {
    position: absolute;
    left: 60px;
    top: 170px;
    display: flex;
    align-items: center;
    gap: 14px;
  }
  .brand__dot {
    width: 26px; height: 26px;
    border-radius: 50%;
    background: var(--green);
  }
  .card--back .brand__name {
    color: var(--paper);
    font-size: 54px;
    font-weight: 400;
    line-height: 1;
  }
  .card--back .site {
    position: absolute;
    left: 104px;
    top: 250px;
    color: var(--paper);
    font-size: 15px;
    letter-spacing: 3px;
  }
  .card--back .site em { font-style: normal; color: var(--green); }

  /* Front side */
  .card--front {
    top: 480px;
    background: linear-gradient(180deg, var(--paper) 0%, var(--paper-shade) 100%);
  }
  .card--front .brand {
    position: absolute;
    left: 44px;
    top: 128px;
    display: flex;
    align-items: center;
    gap: 14px;
  }
  .card--front .brand__name {
    color: var(--ink);
    font-size: 62px;
    font-weight: 400;
    line-height: 1;
  }
  .divider {
    position: absolute;
    left: 292px;
    top: 50px;
    width: 1px;
    height: 150px;
    background: var(--rule);
  }
  .person {
    position: absolute;
    left: 312px;
    top: 48px;
  }
  .person__name {
    color: var(--green);
    font-size: 28px;
    font-weight: 700;
    line-height: 1.05;
  }
  .person__title {
    color: var(--ink);
    font-size: 16px;
    margin-top: 2px;
  }
  .contacts {
    list-style: none;
    margin-top: 14px;
  }
  .contacts li {
    display: flex;
    align-items: center;
    gap: 8px;
    color: var(--ink);
    font-size: 14px;
    line-height: 20px;
  }
  .contacts svg { width: 13px; height: 13px; flex: none; }
  .address-band {
    position: absolute;
    left: 0; right: 0;
    bottom: 22px;
    height: 40px;
    background: var(--charcoal);
    border-top: 2px solid var(--paper);
    border-bottom: 2px solid var(--paper);
    box-shadow: 0 -3px 0 var(--green), 0 3px 0 var(--green);
    color: var(--paper);
    font-size: 15px;
    display: flex;
    align-items: center;
    justify-content: center;
    letter-spacing: 0.3px;
  }
</style>
</head>
<body>
  <section class="card card--back" aria-label="Card back">
    <div class="brand">
      <span class="brand__dot"></span>
      <span class="brand__name">Brovix</span>
    </div>
    <p class="site">www.<em>brovix</em>.example</p>
  </section>

  <section class="card card--front" aria-label="Card front">
    <div class="brand">
      <span class="brand__dot"></span>
      <span class="brand__name">Brovix</span>
    </div>
    <div class="divider"></div>
    <div class="person">
      <h1 class="person__name">Halyna Dorosh</h1>
      <p class="person__title">Director of Marketing</p>
      <ul class="contacts">
        <li>
          <svg viewBox="0 0 14 14" aria-hidden="true"><rect x="3.5" y="1" width="7" height="12" rx="1.5" fill="none" stroke="#7cc242" stroke-width="1.5"/></svg>
          780.555.0184
        </li>
        <li>
          <svg viewBox="0 0 14 14" aria-hidden="true"><path d="M3 1.5l2.5 0.5 0.8 2.6-1.5 1.2a7 7 0 0 0 3.4 3.4l1.2-1.5 2.6 0.8 0.5 2.5-1.8 1.5C5.5 12.5 1.5 8.5 1.5 3.3z" fill="#7cc242"/></svg>
          780.555.0184
        </li>
        <li>
          <svg viewBox="0 0 14 14" aria-hidden="true"><rect x="1" y="3" width="12" height="8.5" fill="#7cc242"/><path d="M1 3l6 5 6-5" fill="none" stroke="#ffffff" stroke-width="1.2"/></svg>
          halya.dorosh@quillmail.example
        </li>
        <li>
          <svg viewBox="0 0 14 14" aria-hidden="true"><circle cx="7" cy="7" r="5.8" fill="none" stroke="#7cc242" stroke-width="1.3"/><ellipse cx="7" cy="7" rx="2.4" ry="5.8" fill="none" stroke="#7cc242" stroke-width="1.1"/><path d="M1.2 7h11.6" stroke="#7cc242" stroke-width="1.1"/></svg>
          www.brovix.example
        </li>
      </ul>
    </div>
    <div class="address-band">20517 - 87 Ave. Edmonton, AB, Canada. T6K 4N8</div>
  </section>
</body>
</html>
```